Industry / Entity Type

Financial consultancy / advisers

Current site is: http://www.brightmoor-counsel.com

Looking for a complete overhaul of this site, we are after a clean modern look. Will require the ability to easily add, update and remove content, hence the WordPress design.
Example:
Add case studies
Industry documentation (downloadable brochures / flyers and such)

What we like from our current site is the colour the fonts and the logo (the city of London) we would like to have other city outlines (NYC and Tokyo, Hong Kong, Singapore).

The site will be used by our potential clients to get in contact and re-view the case studies, if possible would like to have a client login area where they can download our documents like NDA’s etc and T&C’s.

Task Outline

Create a Web Design (Coded - Design and coding required)
Designer must provide full implementation/coding depending on the platform chosen by the client (i.e. WordPress theme, HTML/CSS, bootstrap etc.)

Task Description

I need a full website built that must work on desktop and mobile. I can provide the London city skyline and the font file, which we have used. Some stock industrial photos will be required.

Requirements:

*Splash page
*What We Do
*How We do it
*Who Are We? To have the same information and links as the current site
*Why use us?
*Clients: To have the same information and links as the current site
*Partners: To have the same information and links as the current site
*Contact:

Target Market(s)

Financial institutions trading Equities, Futures, Options, Forex and Fixed Income.
Regulators, Exchanges, ECN’s
Buy side firms and Sell side firms

Industry/Entity Type

Financial

Coding

Coded - Design and coding required

Number of Pages Required

5+ page

Font styles to use
Sans Serif

Colors
f04a50

Requirements
Must have
• Splash page
• What We Do
• How We do it
• Who Are We? To have the same information and links as the current site
• Why use us?
• Clients: To have the same information and links as the current site
• Partners: To have the same information and links as the current site
• Contact:

```html
<!DOCTYPE html>
<html lang="en">
<head>
<meta charset="utf-8">
<title>Brightmoor Counsel</title>
<link href="https://fonts.googleapis.com/css2?family=Michroma&family=Montserrat:wght@600;700&family=Open+Sans:wght@400;600&display=swap" rel="stylesheet">
<style>
:root{
  --brand:#f04a50;
  --ink:#333;
  --text:#555;
  --muted:#888;
  --line:#dcdcdc;
  --white:#fff;
  --footer:#f4f4f4;
}
*{box-sizing:border-box;margin:0;padding:0}
html,body{width:1200px;height:2250px;overflow:hidden;background:var(--white)}
body{font-family:"Open Sans",Arial,sans-serif;color:var(--text);position:relative}
.display{font-family:"Michroma",Arial,sans-serif}

.site-header{position:absolute;left:0;top:0;width:1200px;height:110px}
.brand{position:absolute;left:75px;top:38px;display:flex;align-items:center;gap:12px}
.brand-mark{width:14px;height:14px;background:var(--brand)}
.brand-name{font-family:"Michroma",Arial,sans-serif;font-size:19px;color:var(--ink);letter-spacing:1px;text-transform:uppercase}
.header-contact{position:absolute;top:38px;display:flex;align-items:center;gap:18px}
.icon-box{width:33px;height:33px;border:1.5px solid var(--brand);border-radius:3px;display:flex;align-items:center;justify-content:center}
.phone-contact{left:612px}
.phone-contact span{font-family:"Montserrat",Arial,sans-serif;font-weight:700;font-size:16px;color:var(--ink)}
.mail-contact{left:843px}
.mail-contact span{font-size:14px;color:var(--text);text-transform:uppercase;letter-spacing:.5px}

.main-nav{position:absolute;left:0;top:110px;width:1200px;height:53px;background:var(--brand);display:flex;align-items:center;padding-left:81px;gap:0}
.main-nav a{font-family:"Montserrat",Arial,sans-serif;font-weight:700;font-size:14.5px;color:var(--white);text-decoration:none;text-transform:uppercase;letter-spacing:.4px}
.main-nav a+a{margin-left:46px}

.hero{position:absolute;left:0;top:163px;width:1200px;height:497px;background:linear-gradient(180deg,#4c4f78 0%,#8a6f86 35%,#6b4b45 60%,#2e241f 100%)}
.hero-title{position:absolute;left:0;top:170px;width:1200px;text-align:center;color:var(--white);font-size:41px;line-height:44px;text-transform:uppercase;letter-spacing:1px}
.hero-dots{position:absolute;top:612px;left:563px;display:flex;gap:8px}
.hero-dots i{width:11px;height:11px;border-radius:50%;background:var(--white);display:block}
.hero-dots i.active{background:var(--brand)}

.section-title{text-align:center;color:var(--brand);font-size:25px;text-transform:uppercase;letter-spacing:4px;font-weight:400}
.btn{display:inline-block;border:1.5px solid #333;border-radius:2px;font-family:"Montserrat",Arial,sans-serif;font-weight:600;font-size:12.5px;color:var(--ink);text-transform:uppercase;padding:9px 17px;letter-spacing:.3px}

.welcome{position:absolute;left:0;top:660px;width:1200px;height:318px;text-align:center}
.welcome .section-title{margin-top:50px}
.welcome p{width:1000px;margin:28px auto 0;font-size:14.5px;line-height:25.5px;color:var(--text)}
.welcome .btn{margin-top:40px}

.services{position:absolute;left:0;top:978px;width:1200px;height:417px;background:linear-gradient(90deg,#e9e9e9,#f6f6f6 50%,#e5e5e5)}
.service-card{position:absolute;top:49px;width:330px;height:320px;background:var(--white);box-shadow:0 2px 6px rgba(0,0,0,.25);text-align:center}
.service-card:nth-child(1){left:75px}
.service-card:nth-child(2){left:434px}
.service-card:nth-child(3){left:796px}
.service-icon{width:94px;height:94px;border-radius:50%;background:var(--brand);margin:27px auto 0;display:flex;align-items:center;justify-content:center}
.service-card h3{font-family:"Michroma",Arial,sans-serif;font-weight:400;font-size:19px;color:var(--brand);margin-top:26px;letter-spacing:.5px}
.service-card p{width:260px;margin:10px auto 0;font-size:14.5px;line-height:25px}
.service-card .btn{margin-top:17px}

.logo-band{position:absolute;left:0;width:1200px;text-align:center}
.logo-band .lead{font-size:14.5px;margin-top:22px;color:var(--text)}
.logo-row{position:absolute;left:75px;top:127px;width:1050px;height:80px;display:flex;justify-content:space-between}
.logo-tile{width:251px;height:80px;border:1px solid var(--line);display:flex;align-items:center;justify-content:center;gap:8px;font-family:"Open Sans",Arial,sans-serif;font-weight:600;font-size:19px;color:#2b3e6b}
.logo-tile i{width:10px;height:10px;border-radius:50%;background:#2b3e6b;display:block}
.arrow{position:absolute;top:150px}
.arrow.prev{left:48px}
.arrow.next{left:1138px}
.clients{top:1395px;height:270px}
.clients .section-title{margin-top:40px}
.divider{position:absolute;left:75px;top:1665px;width:1050px;height:1px;background:var(--line)}
.partners{top:1666px;height:260px}
.partners .section-title{margin-top:40px}

.site-footer{position:absolute;left:0;top:1945px;width:1200px;height:305px;background:var(--footer)}
.footer-brand{position:absolute;left:75px;top:45px;width:230px}
.footer-brand .brand-name{font-size:12.5px;display:flex;align-items:center;gap:8px}
.footer-brand .brand-name i{width:10px;height:10px;background:var(--brand);display:block}
.footer-brand p{font-size:13px;line-height:21px;color:var(--muted);margin-top:34px}
.footer-brand .reg{color:var(--brand);margin-top:14px}
.footer-col{position:absolute;top:48px}
.footer-col h4{font-family:"Montserrat",Arial,sans-serif;font-weight:700;font-size:14.5px;color:var(--brand);text-transform:uppercase;letter-spacing:.5px}
.footer-col ul{list-style:none}
.footer-col li{font-size:14px;line-height:34px;color:var(--text)}
.sitemap{left:342px}
.sitemap .lists{display:flex;gap:0;margin-top:10px}
.sitemap ul{width:160px}
.contact-info{left:615px;width:240px}
.contact-info address{font-style:normal;font-size:14px;line-height:22px;margin-top:15px}
.contact-line{display:flex;align-items:center;gap:20px;font-size:14px;margin-top:8px}
.contact-line:first-of-type{margin-top:12px}
.follow{left:885px;width:240px}
.socials{display:flex;flex-wrap:wrap;gap:6px 14px;margin-top:18px;font-size:13px;font-weight:600;color:#999}
</style>
</head>
<body>

<header class="site-header">
  <div class="brand"><i class="brand-mark"></i><span class="brand-name">Brightmoor Counsel</span></div>
  <div class="header-contact phone-contact">
    <div class="icon-box"><svg width="14" height="14" viewBox="0 0 24 24"><path fill="#f04a50" d="M6.6 10.8a15.1 15.1 0 0 0 6.6 6.6l2.2-2.2c.3-.3.7-.4 1-.2 1.1.4 2.3.6 3.6.6.6 0 1 .4 1 1V20c0 .6-.4 1-1 1A17 17 0 0 1 3 4c0-.6.4-1 1-1h3.5c.6 0 1 .4 1 1 0 1.3.2 2.5.6 3.6.1.3 0 .7-.2 1z"/></svg></div>
    <span>44(0)20 5550 1862</span>
  </div>
  <div class="header-contact mail-contact">
    <div class="icon-box"><svg width="15" height="12" viewBox="0 0 20 16"><rect x="0" y="0" width="20" height="16" rx="2" fill="#f04a50"/><path d="M1 2l9 7 9-7" stroke="#fff" stroke-width="2" fill="none"/></svg></div>
    <span>sales@brightmoor-counsel.com</span>
  </div>
</header>

<nav class="main-nav">
  <a>Home</a><a>What we do</a><a>How we do it</a><a>Who are we</a><a>Why use us</a><a>Clients</a><a>Partners</a><a>Contact</a>
</nav>

<section class="hero" role="img" aria-label="City skyline at dusk with a tall skyscraper in the centre">
  <h1 class="hero-title display">Brightmoor<br>Counsel</h1>
</section>
<div class="hero-dots"><i class="active"></i><i></i><i></i><i></i></div>

<section class="welcome">
  <h2 class="section-title display">Welcome to our website</h2>
  <p>Since founding Brightmoor Counsel in 2014 we have dedicated ourselves to the provision of services. What differentiates us from other advisers or consultancies is a genuine motivation to see our clients succeed. Today’s technology allows our clients to take their knowledge to the market in ways that previous generations could only dream of. That’s why BMC is dedicated to seeing you choose the right technology strategy, ensuring you maintain a competitive edge over your peers.</p>
  <span class="btn">Read more</span>
</section>

<section class="services" role="img" aria-label="Faded photo of a business team behind the service cards">
  <article class="service-card">
    <div class="service-icon"><svg width="52" height="46" viewBox="0 0 52 46" fill="#fff"><circle cx="34" cy="9" r="8"/><text x="34" y="13" font-size="11" text-anchor="middle" fill="#f04a50" font-family="Arial">$</text><circle cx="18" cy="18" r="6"/><path d="M6 38c0-8 5-13 12-13s12 5 12 13z"/><circle cx="36" cy="24" r="5"/><path d="M28 38c1-6 4-9 8-9s8 3 8 9z"/><rect x="2" y="39" width="48" height="4"/></svg></div>
    <h3>What We Do</h3>
    <p>Vestibulum ante ipsum primis in faucibus orci luctus et ultrices posuere cubilia magna varius commodo..</p>
    <span class="btn">Read more</span>
  </article>
  <article class="service-card">
    <div class="service-icon"><svg width="54" height="44" viewBox="0 0 54 44" fill="#fff"><circle cx="27" cy="8" r="6"/><path d="M19 22c0-6 4-9 8-9s8 3 8 9z"/><circle cx="10" cy="14" r="5"/><circle cx="44" cy="14" r="5"/><rect x="6" y="24" width="42" height="6" rx="1"/><circle cx="16" cy="36" r="4"/><circle cx="38" cy="36" r="4"/><rect x="10" y="30" width="4" height="12"/><rect x="40" y="30" width="4" height="12"/></svg></div>
    <h3>How We Do It</h3>
    <p>Vestibulum ante ipsum primis in faucibus orci luctus et ultrices posuere cubilia magna varius commodo..</p>
    <span class="btn">Read more</span>
  </article>
  <article class="service-card">
    <div class="service-icon"><svg width="54" height="44" viewBox="0 0 54 44" fill="#fff"><circle cx="27" cy="9" r="7"/><path d="M15 40c0-12 5-20 12-20s12 8 12 20z"/><circle cx="11" cy="14" r="5.5"/><path d="M1 40c0-10 4-16 10-16 3 0 5 1 6 3-2 4-3 8-3 13z"/><circle cx="43" cy="14" r="5.5"/><path d="M53 40c0-10-4-16-10-16-3 0-5 1-6 3 2 4 3 8 3 13z"/></svg></div>
    <h3>Why Use Us</h3>
    <p>Vestibulum ante ipsum primis in faucibus orci luctus et ultrices posuere cubilia magna varius commodo..</p>
    <span class="btn">Read more</span>
  </article>
</section>

<section class="logo-band clients">
  <h2 class="section-title display">Our clients</h2>
  <p class="lead">You will find an impressive list of clients that BMC have worked with.</p>
  <svg class="arrow prev" width="12" height="20" viewBox="0 0 12 20"><path d="M10 2 2 10l8 8" stroke="#bbb" stroke-width="2" fill="none"/></svg>
  <div class="logo-row">
    <div class="logo-tile"><i></i>Corvane</div>
    <div class="logo-tile"><i></i>Tradeloop</div>
    <div class="logo-tile"><i></i>Meridian Reach</div>
    <div class="logo-tile"><i></i>Quaylink</div>
  </div>
  <svg class="arrow next" width="12" height="20" viewBox="0 0 12 20"><path d="M2 2l8 8-8 8" stroke="#bbb" stroke-width="2" fill="none"/></svg>
</section>

<div class="divider"></div>

<section class="logo-band partners">
  <h2 class="section-title display">Our partners</h2>
  <p class="lead">Impressive list of partners, working together, building solutions to drive business</p>
  <svg class="arrow prev" width="12" height="20" viewBox="0 0 12 20"><path d="M10 2 2 10l8 8" stroke="#bbb" stroke-width="2" fill="none"/></svg>
  <div class="logo-row">
    <div class="logo-tile"><i></i>Netvale</div>
    <div class="logo-tile"><i></i>Tradeloop</div>
    <div class="logo-tile"><i></i>Meridian Reach</div>
    <div class="logo-tile"><i></i>Stratum Grid</div>
  </div>
  <svg class="arrow next" width="12" height="20" viewBox="0 0 12 20"><path d="M2 2l8 8-8 8" stroke="#bbb" stroke-width="2" fill="none"/></svg>
</section>

<footer class="site-footer">
  <div class="footer-brand">
    <div class="brand-name"><i></i>Brightmoor Counsel</div>
    <p>Copyright © 2017. Company Name<br>All Right Reserved</p>
    <p class="reg">Company No:07214638<br>VAT No: 5810427</p>
  </div>
  <div class="footer-col sitemap">
    <h4>Site map</h4>
    <div class="lists">
      <ul><li>Home</li><li>What we do</li><li>How we do it</li><li>Who are we</li><li>Why use us</li></ul>
      <ul><li>Clients</li><li>Partners</li><li>Contact</li></ul>
    </div>
  </div>
  <div class="footer-col contact-info">
    <h4>Contact info</h4>
    <address>Suite 4 Harlow Court,<br>Eastmere, Northbury,<br>Beds,<br>NB7 2QL</address>
    <div class="contact-line"><svg width="13" height="13" viewBox="0 0 24 24"><path fill="#555" d="M6.6 10.8a15.1 15.1 0 0 0 6.6 6.6l2.2-2.2c.3-.3.7-.4 1-.2 1.1.4 2.3.6 3.6.6.6 0 1 .4 1 1V20c0 .6-.4 1-1 1A17 17 0 0 1 3 4c0-.6.4-1 1-1h3.5c.6 0 1 .4 1 1 0 1.3.2 2.5.6 3.6.1.3 0 .7-.2 1z"/></svg>44(0)20 5550 1862</div>
    <div class="contact-line"><svg width="14" height="11" viewBox="0 0 20 16"><rect width="20" height="16" rx="2" fill="#555"/><path d="M1 2l9 7 9-7" stroke="#f4f4f4" stroke-width="2" fill="none"/></svg>admin@brightmoor-counsel.com</div>
  </div>
  <div class="footer-col follow">
    <h4>Follow us</h4>
    <div class="socials"><span>Folio</span><span>Chirp</span><span>Netly</span><span>Orbit</span><span>Lens</span><span>Reel</span></div>
  </div>
</footer>

</body>
</html>
```